1" x 3" label needed for essential oil bottle(s) - new ecommerce company

We need a label designed for 10 ml bottles of essential oils. We are offering 9 different types of essential oil: Lavender, Cedarwood, Eucalyptus, Frankincense, Lemon, Orange, Peppermint, Rosemary, and Tea Tree. The label should have a space for the type of essential oil. The bottles are an amber color (am including a photo) as essential oils are sensitive to light. also am including an AI file of our logo, which we'd like included on the label; the logo file also contains our logo colors, a dark blue and light grey. We'd also like the following on the label: "CAUTION: EYE AND SKIN IRRITANT. Avoid contact with eyes and skin. Wash hands after handling. If eye contact occurs, flush with water for 15 minutes. Not intended for topical or internal use. Contains Essential Oils. KEEP OUT OF REACH OF CHILDREN."
Also "Ingredients: 100% pure essential oil, GC tested."
Also "0.33 fl oz (10 ml)
Finally, we will need to include a sideways bar code on the right side of the label, so need 3/8" of white space on the right of the label.
We'd like the label to be calming, but modern, friendly, and confident.

```html
<!DOCTYPE html>
<html lang="en">
<head>
<meta charset="utf-8">
<title>Solvera Essential Oil Labels</title>
<link href="https://fonts.googleapis.com/css2?family=Cinzel:wght@400&family=Cormorant+Garamond:wght@400;500;600&family=Cormorant+SC:wght@400;500&display=swap" rel="stylesheet">
<style>
  :root {
    --canvas: #d9d8d8;
    --label-paper: #efeeec;
    --barcode-space: #ffffff;
    --label-edge: #3a3a3c;
    --hairline: #b9b8b6;
    --ink: #2b2b2d;
    --ink-soft: #5a5a5c;
    --rule-shadow: rgba(60,60,60,0.35);
    --lavender: #9a86b8;
    --cedarwood: #9a7352;
    --eucalyptus: #6f9a94;
    --frankincense: #c9a266;
    --lemon-leaf: #4f8a3c;
    --lemon-name: #3f6f2d;
    --orange-fruit: #d98a4a;
    --orange-name: #c98a5a;
    --mint-leaf: #5f9a5a;
    --rosemary-stem: #9aa39a;
    --teatree-leaf: #3f5a3f;
  }
  * { margin: 0; padding: 0; box-sizing: border-box; }
  html, body { width: 1200px; height: 1000px; overflow: hidden; }
  body { background: var(--canvas); font-family: "Cormorant Garamond", serif; color: var(--ink); }

  .label-set {
    position: absolute; left: 50px; top: 23px; width: 1100px;
    display: flex; flex-direction: column; gap: 9px;
  }
  .label {
    position: relative; height: 98px; background: var(--label-paper);
    border-top: 4px solid var(--label-edge); border-bottom: 4px solid var(--label-edge);
    display: grid; grid-template-columns: 310px 1fr 170px 90px;
  }

  .caution {
    padding: 6px 14px; font-size: 9.5px; line-height: 1.2; color: var(--ink);
    border-right: 1px solid var(--hairline); display: flex; align-items: center;
  }
  .caution strong { font-weight: 600; }

  .front { position: relative; display: flex; align-items: center; justify-content: center; }
  .botanical { position: absolute; top: 8px; bottom: 8px; width: 70px; border-radius: 40% 50% 45% 55%; }
  .botanical--left { left: 22px; }
  .botanical--right { right: 22px; }
  .botanical--lavender { background: radial-gradient(ellipse, var(--lavender), rgba(154,134,184,0.25) 70%, transparent); }
  .botanical--cedarwood { background: radial-gradient(ellipse, var(--cedarwood), rgba(154,115,82,0.25) 70%, transparent); }
  .botanical--eucalyptus { background: radial-gradient(ellipse, var(--eucalyptus), rgba(111,154,148,0.25) 70%, transparent); }
  .botanical--frankincense { background: radial-gradient(ellipse, var(--frankincense), rgba(201,162,102,0.25) 70%, transparent); }
  .botanical--lemon { background: radial-gradient(ellipse, var(--lemon-leaf), rgba(79,138,60,0.25) 70%, transparent); }
  .botanical--orange { background: radial-gradient(ellipse, var(--orange-fruit), rgba(190,150,110,0.35) 65%, transparent); }
  .botanical--mint { background: radial-gradient(ellipse, var(--mint-leaf), rgba(95,154,90,0.25) 70%, transparent); }
  .botanical--rosemary { width: 30px; background: linear-gradient(180deg, transparent, var(--rosemary-stem), transparent); border-radius: 15px; }
  .botanical--rosemary.botanical--left { left: 42px; }
  .botanical--rosemary.botanical--right { right: 42px; }
  .botanical--teatree { background: radial-gradient(ellipse, var(--teatree-leaf), rgba(63,90,63,0.25) 70%, transparent); }

  .label-text { text-align: center; display: flex; flex-direction: column; align-items: center; }
  .brand { display: flex; align-items: center; gap: 7px; }
  .brand-dot { width: 9px; height: 9px; border-radius: 50%; background: var(--ink); }
  .brand-name { font-family: "Cinzel", serif; font-size: 15px; letter-spacing: 4px; line-height: 1.1; }
  .tagline { font-size: 11px; line-height: 1.2; margin-top: 2px; color: var(--ink-soft); }
  .oil-name {
    font-family: "Cormorant SC", serif; font-size: 24px; letter-spacing: 1.5px; line-height: 1;
    margin-top: 2px; text-transform: uppercase; font-weight: 400;
  }
  .oil-name--title { text-transform: none; }
  .oil-rule { width: 80px; height: 4px; margin-top: 2px; border-radius: 50%;
    background: radial-gradient(ellipse, var(--rule-shadow), transparent 70%); }
  .volume { font-size: 11px; line-height: 1.2; margin-top: 1px; }

  .oil-name--lemon { color: var(--lemon-name); }
  .oil-name--orange { color: var(--orange-name); }
  .oil-name--soft { color: var(--ink-soft); }

  .details {
    padding: 6px 12px; font-size: 10.5px; line-height: 1.3; color: var(--ink);
    border-left: 1px solid var(--hairline);
    display: flex; flex-direction: column; justify-content: center; gap: 4px;
  }
  .details strong { font-weight: 600; }
  .barcode-space { background: var(--barcode-space); border-left: 1px solid var(--hairline); }
</style>
</head>
<body>
<main class="label-set">

  <section class="label">
    <p class="caution"><span><strong>CAUTION: EYE AND SKIN IRRITANT.</strong> Avoid contact with eyes and skin. Wash hands after handling. If eye contact occurs, flush with water for 15 minutes. Not intended for topical or internal use. Contains Essential Oils. <strong>KEEP OUT OF REACH OF CHILDREN.</strong></span></p>
    <div class="front">
      <div class="botanical botanical--left botanical--lavender" role="img" aria-label="Lavender sprig illustration"></div>
      <div class="label-text">
        <div class="brand"><span class="brand-dot"></span><span class="brand-name">SOLVERA</span></div>
        <p class="tagline">100% pure essential oil</p>
        <h2 class="oil-name oil-name--soft">Lavender</h2>
        <div class="oil-rule"></div>
        <p class="volume">0.33 fl oz (10 ml)</p>
      </div>
      <div class="botanical botanical--right botanical--lavender" role="img" aria-label="Lavender sprig illustration"></div>
    </div>
    <div class="details"><p><strong>Ingredients:</strong> 100% pure essential oil, GC tested.</p><p>0.33 fl oz (10 ml)</p></div>
    <div class="barcode-space"></div>
  </section>

  <section class="label">
    <p class="caution"><span><strong>CAUTION: EYE AND SKIN IRRITANT.</strong> Avoid contact with eyes and skin. Wash hands after handling. If eye contact occurs, flush with water for 15 minutes. Not intended for topical or internal use. Contains Essential Oils. <strong>KEEP OUT OF REACH OF CHILDREN.</strong></span></p>
    <div class="front">
      <div class="botanical botanical--left botanical--cedarwood" role="img" aria-label="Cedar branch illustration"></div>
      <div class="label-text">
        <div class="brand"><span class="brand-dot"></span><span class="brand-name">SOLVERA</span></div>
        <p class="tagline">100% pure essential oil</p>
        <h2 class="oil-name oil-name--soft">Cedarwood</h2>
        <div class="oil-rule"></div>
        <p class="volume">0.33 fl oz (10 ml)</p>
      </div>
      <div class="botanical botanical--right botanical--cedarwood" role="img" aria-label="Cedar cone illustration"></div>
    </div>
    <div class="details"><p><strong>Ingredients:</strong> 100% pure essential oil, GC tested.</p><p>0.33 fl oz (10 ml)</p></div>
    <div class="barcode-space"></div>
  </section>

  <section class="label">
    <p class="caution"><span><strong>CAUTION: EYE AND SKIN IRRITANT.</strong> Avoid contact with eyes and skin. Wash hands after handling. If eye contact occurs, flush with water for 15 minutes. Not intended for topical or internal use. Contains Essential Oils. <strong>KEEP OUT OF REACH OF CHILDREN.</strong></span></p>
    <div class="front">
      <div class="botanical botanical--left botanical--eucalyptus" role="img" aria-label="Eucalyptus leaves illustration"></div>
      <div class="label-text">
        <div class="brand"><span class="brand-dot"></span><span class="brand-name">SOLVERA</span></div>
        <p class="tagline">100% pure essential oil</p>
        <h2 class="oil-name oil-name--soft">Eucalyptus</h2>
        <div class="oil-rule"></div>
        <p class="volume">0.33 fl oz (10 ml)</p>
      </div>
      <div class="botanical botanical--right botanical--eucalyptus" role="img" aria-label="Eucalyptus leaves illustration"></div>
    </div>
    <div class="details"><p><strong>Ingredients:</strong> 100% pure essential oil, GC tested.</p><p>0.33 fl oz (10 ml)</p></div>
    <div class="barcode-space"></div>
  </section>

  <section class="label">
    <p class="caution"><span><strong>CAUTION: EYE AND SKIN IRRITANT.</strong> Avoid contact with eyes and skin. Wash hands after handling. If eye contact occurs, flush with water for 15 minutes. Not intended for topical or internal use. Contains Essential Oils. <strong>KEEP OUT OF REACH OF CHILDREN.</strong></span></p>
    <div class="front">
      <div class="botanical botanical--left botanical--frankincense" role="img" aria-label="Frankincense resin and branch illustration"></div>
      <div class="label-text">
        <div class="brand"><span class="brand-dot"></span><span class="brand-name">SOLVERA</span></div>
        <p class="tagline">100% pure essential oil</p>
        <h2 class="oil-name oil-name--soft">Frankincense</h2>
        <div class="oil-rule"></div>
        <p class="volume">0.33 fl oz (10 ml)</p>
      </div>
      <div class="botanical botanical--right botanical--frankincense" role="img" aria-label="Frankincense branch illustration"></div>
    </div>
    <div class="details"><p><strong>Ingredients:</strong> 100% pure essential oil, GC tested.</p><p>0.33 fl oz (10 ml)</p></div>
    <div class="barcode-space"></div>
  </section>

  <section class="label">
    <p class="caution"><span><strong>CAUTION: EYE AND SKIN IRRITANT.</strong> Avoid contact with eyes and skin. Wash hands after handling. If eye contact occurs, flush with water for 15 minutes. Not intended for topical or internal use. Contains Essential Oils. <strong>KEEP OUT OF REACH OF CHILDREN.</strong></span></p>
    <div class="front">
      <div class="botanical botanical--left botanical--lemon" role="img" aria-label="Lemon leaf and blossom illustration"></div>
      <div class="label-text">
        <div class="brand"><span class="brand-dot"></span><span class="brand-name">SOLVERA</span></div>
        <p class="tagline">100% pure essential oil</p>
        <h2 class="oil-name oil-name--lemon">Lemon</h2>
        <div class="oil-rule"></div>
        <p class="volume">0.33 fl oz (10 ml)</p>
      </div>
      <div class="botanical botanical--right botanical--lemon" role="img" aria-label="Lemon leaf illustration"></div>
    </div>
    <div class="details"><p><strong>Ingredients:</strong> 100% pure essential oil, GC tested.</p><p>0.33 fl oz (10 ml)</p></div>
    <div class="barcode-space"></div>
  </section>

  <section class="label">
    <p class="caution"><span><strong>CAUTION: EYE AND SKIN IRRITANT.</strong> Avoid contact with eyes and skin. Wash hands after handling. If eye contact occurs, flush with water for 15 minutes. Not intended for topical or internal use. Contains Essential Oils. <strong>KEEP OUT OF REACH OF CHILDREN.</strong></span></p>
    <div class="front">
      <div class="botanical botanical--left botanical--orange" role="img" aria-label="Orange branch with fruit illustration"></div>
      <div class="label-text">
        <div class="brand"><span class="brand-dot"></span><span class="brand-name">SOLVERA</span></div>
        <p class="tagline">100% pure essential oil</p>
        <h2 class="oil-name oil-name--orange">Orange</h2>
        <div class="oil-rule"></div>
        <p class="volume">0.33 fl oz (10 ml)</p>
      </div>
      <div class="botanical botanical--right botanical--orange" role="img" aria-label="Orange fruit illustration"></div>
    </div>
    <div class="details"><p><strong>Ingredients:</strong> 100% pure essential oil, GC tested.</p><p>0.33 fl oz (10 ml)</p></div>
    <div class="barcode-space"></div>
  </section>

  <section class="label">
    <p class="caution"><span><strong>CAUTION: EYE AND SKIN IRRITANT.</strong> Avoid contact with eyes and skin. Wash hands after handling. If eye contact occurs, flush with water for 15 minutes. Not intended for topical or internal use. Contains Essential Oils. <strong>KEEP OUT OF REACH OF CHILDREN.</strong></span></p>
    <div class="front">
      <div class="botanical botanical--left botanical--mint" role="img" aria-label="Peppermint leaves illustration"></div>
      <div class="label-text">
        <div class="brand"><span class="brand-dot"></span><span class="brand-name">SOLVERA</span></div>
        <p class="tagline">100% pure essential oil</p>
        <h2 class="oil-name oil-name--soft">Peppermint</h2>
        <div class="oil-rule"></div>
        <p class="volume">0.33 fl oz (10 ml)</p>
      </div>
      <div class="botanical botanical--right botanical--mint" role="img" aria-label="Peppermint leaves illustration"></div>
    </div>
    <div class="details"><p><strong>Ingredients:</strong> 100% pure essential oil, GC tested.</p><p>0.33 fl oz (10 ml)</p></div>
    <div class="barcode-space"></div>
  </section>

  <section class="label">
    <p class="caution"><span><strong>CAUTION: EYE AND SKIN IRRITANT.</strong> Avoid contact with eyes and skin. Wash hands after handling. If eye contact occurs, flush with water for 15 minutes. Not intended for topical or internal use. Contains Essential Oils. <strong>KEEP OUT OF REACH OF CHILDREN.</strong></span></p>
    <div class="front">
      <div class="botanical botanical--left botanical--rosemary" role="img" aria-label="Rosemary sprig illustration"></div>
      <div class="label-text">
        <div class="brand"><span class="brand-dot"></span><span class="brand-name">SOLVERA</span></div>
        <p class="tagline">100% pure essential oil</p>
        <h2 class="oil-name oil-name--soft">Rosemary</h2>
        <div class="oil-rule"></div>
        <p class="volume">0.33 fl oz (10 ml)</p>
      </div>
      <div class="botanical botanical--right botanical--rosemary" role="img" aria-label="Rosemary sprig illustration"></div>
    </div>
    <div class="details"><p><strong>Ingredients:</strong> 100% pure essential oil, GC tested.</p><p>0.33 fl oz (10 ml)</p></div>
    <div class="barcode-space"></div>
  </section>

  <section class="label">
    <p class="caution"><span><strong>CAUTION: EYE AND SKIN IRRITANT.</strong> Avoid contact with eyes and skin. Wash hands after handling. If eye contact occurs, flush with water for 15 minutes. Not intended for topical or internal use. Contains Essential Oils. <strong>KEEP OUT OF REACH OF CHILDREN.</strong></span></p>
    <div class="front">
      <div class="botanical botanical--left botanical--teatree" role="img" aria-label="Tea tree branch illustration"></div>
      <div class="label-text">
        <div class="brand"><span class="brand-dot"></span><span class="brand-name">SOLVERA</span></div>
        <p class="tagline">100% pure essential oil</p>
        <h2 class="oil-name oil-name--title">Tea Tree</h2>
        <div class="oil-rule"></div>
        <p class="volume">0.33 fl oz (10 ml)</p>
      </div>
      <div class="botanical botanical--right botanical--teatree" role="img" aria-label="Tea tree leaves illustration"></div>
    </div>
    <div class="details"><p><strong>Ingredients:</strong> 100% pure essential oil, GC tested.</p><p>0.33 fl oz (10 ml)</p></div>
    <div class="barcode-space"></div>
  </section>

</main>
</body>
</html>
```